Pebble Tracks - explore habits of productive people

Pebble Tracks is a social place around habits and productivity

The full brief below:

https://notes.brimwellpad.net/page/d/7Qx-RtVmPLa93KwBz-H-cNmq2YeTsRfvUdGkHpXwaB/view?mode=shared

Colors

Designer to choose colors to be used in the design.

Requirements
Must have
• - a feed page to display habits
• - a habit page to add a habit
• / clean, no cluttered design, lots of white space
• / inspired by material design or other design system
Nice to have
• - user page

```html
<!DOCTYPE html>
<html lang="en">
<head>
<meta charset="utf-8">
<title>Pebble Tracks – Feed</title>
<link href="https://fonts.googleapis.com/css2?family=Poppins:wght@400;500;600&display=swap" rel="stylesheet">
<style>
:root{
  --bg:#eef2f6;
  --white:#ffffff;
  --ink:#2b2f36;
  --muted:#6b7280;
  --line:#e3e7ec;
  --panel:#ececec;
  --brand:#1a5fb4;
  --brand-light:#1e9be0;
  --link:#2a4aa6;
  --online:#56c22e;
}
*{box-sizing:border-box;margin:0;padding:0}
html,body{width:850px;height:1200px;overflow:hidden}
body{background:var(--bg);font-family:'Poppins',sans-serif;color:var(--ink);position:relative}
.topbar{position:absolute;left:0;top:0;width:850px;height:56px;background:var(--white);border-bottom:1px solid var(--line)}
.brand{position:absolute;left:72px;top:13px;display:flex;align-items:center;gap:8px}
.brand-mark{width:26px;height:26px;background:var(--brand);border-radius:3px}
.brand-name{font-weight:600;font-size:20px;color:var(--ink)}
.add-habit{position:absolute;left:457px;top:18px;display:flex;align-items:center;gap:6px;font-size:11px}
.tools{position:absolute;left:547px;top:17px;display:flex;gap:8px}
.tool{width:22px;height:22px;border:1px solid #9aa3ad;border-radius:50%}
.account{position:absolute;left:648px;top:14px;display:flex;align-items:center;gap:8px;font-size:8px;line-height:12px}
.account .avatar{width:24px;height:24px;border-radius:50%;background:linear-gradient(#8a9099,#3a3f47)}
.account b{font-weight:600}
.sidebar{position:absolute;left:73px;top:83px;width:178px;height:1002px;background:var(--white);box-shadow:0 0 3px rgba(0,0,0,.15)}
.profile{height:245px;background:var(--panel);text-align:center;padding-top:18px}
.profile .photo{width:76px;height:76px;border-radius:50%;margin:0 auto;border:3px solid var(--white);background:linear-gradient(#c9ccd1,#4a4f57)}
.profile h2{font-weight:500;font-size:12px;margin-top:13px}
.status{font-size:8.5px;margin-top:4px;display:flex;justify-content:center;align-items:center;gap:4px}
.status i{width:6px;height:6px;border-radius:50%;background:var(--online);display:inline-block}
.profile p{font-size:9px;line-height:16px;margin:6px 24px 0}
.menu{list-style:none}
.menu li{height:36px;display:flex;align-items:center;padding-left:14px;gap:16px;font-size:10px;border-bottom:1px solid var(--line)}
.menu li.active{background:linear-gradient(90deg,var(--brand),var(--brand-light));color:var(--white);border:0}
.menu svg{width:16px;height:16px}
.page-title{position:absolute;left:274px;top:80px;font-size:16px;font-weight:500}
.post{position:absolute;left:275px;width:502px;background:var(--white);border:1px solid var(--line);box-shadow:0 0 2px rgba(0,0,0,.06)}
.post-head{display:flex;align-items:flex-start;padding:10px 0 0 16px;gap:10px}
.post-head .avatar{width:34px;height:34px;border-radius:50%;background:linear-gradient(#b59b86,#3b2f28)}
.author{font-size:10.5px;color:var(--link);margin-top:3px;display:flex;align-items:center;gap:22px}
.author i{width:5px;height:5px;border-radius:50%;background:#b0b6bd;display:inline-block}
.date{font-size:8px;color:var(--muted);margin-top:1px}
.post-body{padding:12px 14px 0 15px;font-size:9.4px;line-height:21.5px}
.media{margin:8px 0 0 14px;width:454px;height:106px}
.coffee{background:linear-gradient(90deg,#7a5c45,#5a3f2c 45%,#e9e4de 55%,#3a2216 75%,#2a1a12)}
.group{background:linear-gradient(90deg,#6b8aa5,#d9c2a5 30%,#c9cdd2 55%,#3d5a7a 80%,#b8bcc2)}
.post-foot{position:absolute;left:0;right:0;bottom:0;height:26px;border-top:1px solid var(--line);display:flex;align-items:center;font-size:8px}
.post-foot .comment-input{flex:0 0 339px;padding-left:15px;color:var(--ink)}
.actions{flex:1;height:100%;border-left:1px solid var(--line);display:flex;align-items:center;justify-content:space-around;font-size:6.5px;letter-spacing:.2px}
.actions span{display:flex;align-items:center;gap:3px}
.actions b{width:6px;height:6px;border-radius:1px;background:#555;display:inline-block}
.footer{position:absolute;left:0;width:850px;top:1137px;text-align:center;font-size:9px;padding-right:90px}
</style>
</head>
<body>
<header class="topbar">
  <div class="brand"><span class="brand-mark"></span><span class="brand-name">Pebble Tracks</span></div>
  <div class="add-habit">Add Habit
    <svg width="20" height="20" viewBox="0 0 20 20"><circle cx="10" cy="10" r="10" fill="#1e9be0"/><path d="M10 5v10M5 10h10" stroke="#fff" stroke-width="2.4"/></svg>
  </div>
  <div class="tools"><span class="tool"></span><span class="tool"></span><span class="tool"></span></div>
  <div class="account"><span class="avatar" role="img" aria-label="User portrait"></span>
    <div>Welcome, <b>Marla Venn!</b> ▾<br>3/19/2018 7:19:36 AM</div>
  </div>
</header>

<aside class="sidebar">
  <div class="profile">
    <div class="photo" role="img" aria-label="Profile portrait"></div>
    <h2>Owen Hartley</h2>
    <div class="status"><i></i>Online ▾</div>
    <p>Sed ut perspiciatis unde omnis iste natus error sit vtem accusantium doloremque laudantium, totam rem</p>
  </div>
  <ul class="menu">
    <li><svg viewBox="0 0 16 16"><rect x="1" y="2" width="14" height="12" fill="none" stroke="#1a5fb4" stroke-width="1.5"/><path d="M1 6h14M1 10h14M6 2v12M11 2v12" stroke="#1a5fb4"/></svg>Dashboard</li>
    <li class="active"><svg viewBox="0 0 16 16"><circle cx="8" cy="8" r="6.5" fill="none" stroke="#fff" stroke-width="1.5"/><path d="M5 9.5q3 3 6 0" fill="none" stroke="#fff" stroke-width="1.3"/></svg>Feed</li>
    <li><svg viewBox="0 0 16 16"><rect x="3" y="1" width="10" height="14" fill="#1a5fb4"/></svg>Groups</li>
    <li><svg viewBox="0 0 16 16"><circle cx="4" cy="5" r="2.5" fill="#1a5fb4"/><circle cx="12" cy="5" r="2.5" fill="#1a5fb4"/><circle cx="8" cy="7" r="2.5" fill="#1a5fb4"/><path d="M0 13q4-6 8 0M8 13q4-6 8 0M3 15q5-7 10 0" fill="#1a5fb4"/></svg>Team</li>
    <li><svg viewBox="0 0 16 16"><circle cx="8" cy="5" r="3.5" fill="#1a5fb4"/><path d="M2 15q0-6 6-6t6 6z" fill="#1a5fb4"/></svg>Users</li>
  </ul>
</aside>

<h1 class="page-title">FEED</h1>

<article class="post" style="top:118px;height:286px">
  <div class="post-head"><span class="avatar" role="img" aria-label="Author portrait"></span><div><div class="author">Owen Hartley <i></i></div><div class="date">December 12, 2018</div></div></div>
  <div class="post-body">
    <p>After I pour my morning cup of coffee, I will meditate for sixty seconds.</p>
    <p>After I meditate for sixty seconds, I will write my to-do list for the day.</p>
    <p>After I write my to-do list for the day, I will immediately begin my first task.</p>
  </div>
  <div class="media coffee" role="img" aria-label="Cup of coffee on a wooden table with scattered coffee beans"></div>
  <div class="post-foot"><span class="comment-input">Add comment</span><div class="actions"><span><b></b>LIKE</span><span><b></b>COMMENT</span><span><b></b>SHARE</span></div></div>
</article>

<article class="post" style="top:424px;height:167px">
  <div class="post-head"><span class="avatar" role="img" aria-label="Author portrait"></span><div><div class="author">Owen Hartley <i></i></div><div class="date">December 12, 2018</div></div></div>
  <div class="post-body">
    <p>Sed ut perspiciatis unde omnis iste natus error sit voluptatem accusantium doloremque laudantium</p>
    <p>totam rem aperiam, eaque ipsa quae ab illo inventore veritatis et quasi architecto beatae</p>
    <p>vitae dicta sunt explicabo. Nemo enim ipsam voluptatem quia voluptas sit aspernatur</p>
  </div>
  <div class="post-foot"><span class="comment-input">Add comment</span><div class="actions"><span><b></b>LIKE</span><span><b></b>COMMENT</span><span><b></b>SHARE</span></div></div>
</article>

<article class="post" style="top:611px;height:167px">
  <div class="post-head"><span class="avatar" role="img" aria-label="Author portrait"></span><div><div class="author">Owen Hartley <i></i></div><div class="date">December 12, 2018</div></div></div>
  <div class="post-body">
    <p>After I finish eating dinner, I will put my plate directly into the dishwasher.</p>
    <p>After I put my dishes away, I will immediately wipe down the counter.</p>
    <p>After I wipe down the counter, I will set out my coffee mug for tomorrow morning.</p>
  </div>
  <div class="post-foot"><span class="comment-input">Add comment</span><div class="actions"><span><b></b>LIKE</span><span><b></b>COMMENT</span><span><b></b>SHARE</span></div></div>
</article>

<article class="post" style="top:798px;height:287px">
  <div class="post-head"><span class="avatar" role="img" aria-label="Author portrait"></span><div><div class="author">Owen Hartley <i></i></div><div class="date">December 12, 2018</div></div></div>
  <div class="post-body">
    <p>When I see a set of stairs, I will take them instead of using the elevator.</p>
    <p>Social skills. When I walk into a party, I will introduce myself to anyone I don't know yet.</p>
    <p>When I want to buy something over $100, I will wait 24 hours before purchasing.</p>
  </div>
  <div class="media group" role="img" aria-label="Group of young people talking together at a meetup"></div>
  <div class="post-foot"><span class="comment-input">Add comment</span><div class="actions"><span><b></b>LIKE</span><span><b></b>COMMENT</span><span><b></b>SHARE</span></div></div>
</article>

<footer class="footer">©2018 Pebble Tracks, All Rights Reserved.</footer>
</body>
</html>
```